Brell Stone Company Business Cards

Front and Back Business Card - logo and text setup - cool design. I need workable photoshop or illustrator files so I can setup each employee card with design that is created
Updates

Hi everyone, thank you for the great entries. Please no more white and blue cards - there are so many already - black and silver only now please. thanks!

Target Market(s)

Construction Industry - Facility Managers

Industry/Entity Type

Construction

Contact Information for Business Card

I really like contemporary simplistic looks - clean neat....not opposed to seeing some black backrounds

Requirements
Must have
• Logo/website address with design on front only - www.brellstone-example.com (logo attached)
• Back:
• Name/Title/Company Address/Phone/email address
Nice to have
• Cool design
Should not have
• Nothing gimmicky like Fire or Water - since we are a Fire Protection company - it has all been done

```html
<!DOCTYPE html>
<html lang="en">
<head>
<meta charset="utf-8">
<title>Brell Stone Company – Business Cards</title>
<link href="https://fonts.googleapis.com/css2?family=Lato:wght@300;400;700&family=Oswald:wght@500&display=swap" rel="stylesheet">
<style>
  :root {
    --backdrop: #141416;
    --card: #29292b;
    --silver-light: #f2f2f4;
    --silver-dark: #8e8f94;
    --accent-blue: #3a4a8c;
    --text-light: #c9c9cc;
    --text-muted: #9a9a9e;
    --logo-silver: #d4d4d7;
    --divider: #6a6a6e;
  }
  * { box-sizing: border-box; margin: 0; padding: 0; }
  html, body {
    width: 1200px; height: 912px; overflow: hidden;
    background: var(--backdrop);
    font-family: "Lato", sans-serif;
  }
  .sheet {
    position: relative; width: 1200px; height: 912px;
    display: flex; flex-direction: column; align-items: center;
    justify-content: center; gap: 56px;
  }
  .card {
    position: relative; width: 640px; height: 366px;
    background: var(--card); overflow: hidden;
    box-shadow: 0 18px 40px rgba(0,0,0,.55);
  }
  /* Front */
  .card__edges { position: absolute; inset: 0; width: 100%; height: 100%; }
  .brand {
    position: absolute; left: 0; right: 0; top: 120px;
    display: flex; align-items: center; justify-content: center; gap: 16px;
  }
  .brand__mark { width: 22px; height: 22px; background: var(--logo-silver); }
  .brand__name {
    font-family: "Lato", sans-serif; font-weight: 700;
    font-size: 56px; letter-spacing: -0.5px; color: var(--logo-silver);
  }
  .front__web {
    position: absolute; left: 0; right: 0; top: 250px;
    text-align: center; font-size: 17px; letter-spacing: 0.5px;
    color: var(--text-muted);
  }
  /* Back */
  .back__band {
    position: absolute; left: 0; right: 0; bottom: 0; height: 9px;
    background: var(--accent-blue);
  }
  .person {
    position: absolute; right: 340px; top: 168px; text-align: right;
  }
  .person__name {
    font-family: "Oswald", sans-serif; font-weight: 500;
    font-size: 27px; letter-spacing: -0.3px; text-transform: uppercase;
    color: var(--accent-blue); line-height: 1.1;
  }
  .person__title {
    font-size: 19px; font-weight: 400; color: var(--text-light); margin-top: 2px;
  }
  .back__divider {
    position: absolute; left: 326px; top: 118px; width: 1px; height: 128px;
    background: var(--divider);
  }
  .contact {
    position: absolute; left: 352px; top: 114px;
    color: var(--text-light); font-size: 16px; font-weight: 300; line-height: 1.35;
  }
  .contact__address { margin-bottom: 14px; }
  .contact__list { list-style: none; }
  .contact__item { display: flex; align-items: center; gap: 10px; }
  .contact__icon { width: 13px; height: 13px; flex: none; }
</style>
</head>
<body>
<main class="sheet">

  <section class="card card--front" aria-label="Card front">
    <svg class="card__edges" viewBox="0 0 640 366" preserveAspectRatio="none" aria-hidden="true">
      <defs>
        <linearGradient id="silverLeft" x1="0" x2="1" y1="0" y2="0">
          <stop offset="0" stop-color="var(--silver-dark)"/>
          <stop offset="0.6" stop-color="var(--silver-light)"/>
          <stop offset="1" stop-color="var(--silver-dark)"/>
        </linearGradient>
        <linearGradient id="silverRight" x1="1" x2="0" y1="0" y2="0">
          <stop offset="0" stop-color="var(--silver-dark)"/>
          <stop offset="0.6" stop-color="var(--silver-light)"/>
          <stop offset="1" stop-color="var(--silver-dark)"/>
        </linearGradient>
      </defs>
      <path d="M0,0 C30,60 70,180 52,366 L0,366 Z" fill="url(#silverLeft)"/>
      <path d="M0,0 L0,366" stroke="var(--accent-blue)" stroke-width="5"/>
      <path d="M640,0 C610,60 570,180 588,366 L640,366 Z" fill="url(#silverRight)"/>
      <path d="M640,0 L640,366" stroke="var(--accent-blue)" stroke-width="5"/>
    </svg>
    <div class="brand">
      <span class="brand__mark" aria-hidden="true"></span>
      <span class="brand__name">Brell Stone</span>
    </div>
    <p class="front__web">www.brellstone-example.com</p>
  </section>

  <section class="card card--back" aria-label="Card back">
    <div class="person">
      <h1 class="person__name">Dana Whitfield Moore</h1>
      <p class="person__title">President</p>
    </div>
    <span class="back__divider" aria-hidden="true"></span>
    <div class="contact">
      <p class="contact__address">48 Meridian Way<br>Harlow Point, NY 10990</p>
      <ul class="contact__list">
        <li class="contact__item">
          <svg class="contact__icon" viewBox="0 0 16 16" aria-hidden="true"><path d="M4 1 L6.5 4.5 L5 6 C6 8.5 7.5 10 10 11 L11.5 9.5 L15 12 L13 15 C7 15 1 9 1 3 Z" fill="var(--accent-blue)"/></svg>
          <span>(555) 204-7318</span>
        </li>
        <li class="contact__item">
          <svg class="contact__icon" viewBox="0 0 16 16" aria-hidden="true"><rect x="1" y="3" width="14" height="10" fill="var(--accent-blue)"/><path d="M1 3 L8 9 L15 3" stroke="var(--card)" stroke-width="1.4" fill="none"/></svg>
          <span>info@brellstone-example.com</span>
        </li>
        <li class="contact__item">
          <svg class="contact__icon" viewBox="0 0 16 16" aria-hidden="true"><circle cx="8" cy="8" r="7" fill="var(--accent-blue)"/><path d="M1 8 H15 M8 1 C4 5 4 11 8 15 M8 1 C12 5 12 11 8 15" stroke="var(--card)" stroke-width="1" fill="none"/></svg>
          <span>www.brellstone-example.com</span>
        </li>
      </ul>
    </div>
    <span class="back__band" aria-hidden="true"></span>
  </section>

</main>
</body>
</html>
```